Lumvra App | Pre-Launch Homepage

Dear designer,
Lumvra is a soon to be launched innovative & free social platform for collaborative addictions quitting.
We require a design for our pre-launch homepage that will elevate our basic wireframes to the next level.
We would like the wireframes to serve as a guideline only, and not as a final version of the design. If you have cool ideas - we would appreciate your creativity!
* This is a pre-launch website for a mobile app, and as such the design must be consistent with the general style, design and atmosphere of the app (see screenshot in the shared Drive link).
* We liked the style and feel of the following website: http://tandelhub.example/ - Please let's use it as a reference as well.
* The existing text in the wireframes is there just to represent a place for text. Copy will be edited by us after the design is done.
Please find the wireframes attached, and all relevant design assets and app screenshots in the following Drive shared link -
https://files.example-share.net/open?id=7KQ204RtP3mNxa8Y2Lb61H9cdVzQ
Thanks,
Reginald
Industry/Entity Type
Social
Number of Pages Required
1 page
Look and feel
Each slider illustrates characteristics of the customer's brand and the style your logo design should communicate.

```html
<!DOCTYPE html>
<html lang="en">
<head>
<meta charset="utf-8">
<title>Lumvra App | Pre-Launch Homepage</title>
<link rel="stylesheet" href="https://fonts.googleapis.com/css2?family=Open+Sans:wght@400;600;700&family=Oswald:wght@400;500&display=swap">
<style>
:root{
  --orange:#f39200;
  --orange-dark:#dc7d00;
  --orange-soft:#f7a832;
  --gold:#f6b21b;
  --peach:#f6e3c8;
  --ink:#2e241f;
  --ink-deep:#1f1915;
  --text:#555;
  --muted:#8a8a8a;
  --line:#dcdcdc;
  --paper:#ffffff;
  --beige:#efece3;
  --teal:#3aa6c9;
  --trophy:#f0a36a;
}
*{box-sizing:border-box;margin:0;padding:0}
html,body{width:1200px;height:4644px;overflow:hidden}
body{font-family:"Open Sans",Arial,sans-serif;color:var(--text);background:var(--paper);position:relative}

/* hero */
.hero{position:absolute;left:0;top:0;width:1200px;height:688px;background:linear-gradient(160deg,#3d3c3e 0%,#2c2623 45%,#4d301b 100%);overflow:hidden}
.hero-photo{position:absolute;left:700px;top:40px;width:500px;height:648px;background:radial-gradient(ellipse at 55% 35%,rgba(214,170,140,.55) 0%,rgba(120,90,70,.35) 35%,rgba(30,28,30,0) 70%)}
.hero-phone{position:absolute;left:790px;top:70px;width:250px;height:460px;border-radius:38px;background:linear-gradient(160deg,#4a4a4c,#121212 70%);transform:rotate(14deg);box-shadow:0 20px 50px rgba(0,0,0,.5)}
.hero-phone .screen{position:absolute;left:14px;right:14px;top:64px;bottom:64px;background:linear-gradient(180deg,#3e322b,#1b1817)}
.brand{position:absolute;left:68px;top:40px;font-weight:700;font-size:44px;color:var(--orange);display:flex;align-items:center;gap:12px}
.brand-dot{width:22px;height:22px;border-radius:50%;background:var(--orange)}
.contact-tab{position:absolute;right:40px;top:0;width:168px;height:40px;background:var(--orange);color:#fff;font-weight:600;font-size:17px;text-align:center;line-height:40px;border-radius:0 0 4px 4px}
.hero-title{position:absolute;left:72px;top:222px;width:880px;color:#fff;font-size:36px;line-height:46px;font-weight:400}
.subscribe-row{position:absolute;left:72px;top:380px;display:flex;align-items:center;gap:18px;color:#fff;font-size:23px;line-height:29px;width:460px}
.signup{position:absolute;display:flex;height:44px;background:#fff;border-radius:3px;padding:6px}
.signup .field{flex:1;font-size:15px;color:var(--muted);line-height:32px;padding-left:12px}
.signup .btn{background:var(--orange);color:#fff;font-size:14px;font-weight:700;padding:0 18px;line-height:32px;border-radius:2px}
.hero .signup{left:72px;top:466px;width:440px}
.devices{position:absolute;left:72px;top:590px;display:flex;align-items:flex-end;gap:34px}
.pointer{position:absolute;left:198px;top:672px;width:0;height:0;border-left:16px solid transparent;border-right:16px solid transparent;border-bottom:16px solid var(--orange)}

/* features band */
.features{position:absolute;left:0;top:688px;width:1200px;height:512px;background:var(--orange)}
.feature{position:absolute;top:92px;width:300px;text-align:center}
.feature-badge{width:184px;height:184px;border-radius:50%;background:var(--orange-dark);margin:0 auto;display:flex;align-items:center;justify-content:center}
.feature-badge .disk{width:128px;height:128px;border-radius:50%;background:var(--peach);display:flex;align-items:center;justify-content:center}
.feature-badge .art{width:92px;height:92px;border-radius:50%;background:radial-gradient(circle at 50% 40%,#f0c089 0%,#c97d2e 60%,rgba(246,227,200,0) 72%)}
.feature h3{margin-top:8px;color:#fff;font-size:21px;font-weight:600}
.feature p{margin:10px auto 0;width:260px;color:#fff3df;font-size:14px;line-height:20px}

/* phones */
.phone{position:absolute;border-radius:44px;background:linear-gradient(160deg,#4a4a4c 0%,#1a1a1a 40%,#0d0d0d 100%);box-shadow:inset 0 0 0 3px #6a6a6c}
.phone::before{content:"";position:absolute;left:50%;top:34px;width:56px;height:7px;margin-left:-28px;border-radius:4px;background:#333}
.phone::after{content:"";position:absolute;left:50%;bottom:18px;width:46px;height:46px;margin-left:-23px;border-radius:50%;border:3px solid #3a3a3a}
.phone .screen{position:absolute;left:16px;right:16px;top:76px;bottom:80px;background:#fff;overflow:hidden}
.phone .screen.glow-orange{background:radial-gradient(circle at 50% 50%,#f8b233 0%,#f9c66a 22%,#fde9c4 40%,#fff 62%)}
.phone .screen.glow-gold{background:radial-gradient(circle at 50% 48%,#fbd13c 0%,#f9b62a 20%,#fde6b0 40%,#fff 62%)}
.phone .screen.glow-trophy{background:radial-gradient(ellipse at 50% 55%,#f6b21b 0%,#f8c55a 24%,#fde9c0 44%,#fff 66%)}
.phone .screen.app{background:linear-gradient(180deg,#3e322b,#1c1918)}
.app-bar{position:absolute;left:0;right:0;top:0;height:34px;background:rgba(0,0,0,.35)}
.app-avatar{position:absolute;left:50%;top:54px;width:64px;height:64px;margin-left:-32px;border-radius:50%;background:radial-gradient(circle,#8a6a55,#4a3a30);border:3px solid var(--orange)}
.app-name{position:absolute;left:0;right:0;top:128px;text-align:center;color:#e8ddd4;font-size:12px}
.app-track{position:absolute;left:18px;right:18px;height:6px;border-radius:3px;background:rgba(255,255,255,.15)}
.app-track i{position:absolute;left:0;top:0;bottom:0;border-radius:3px;background:var(--orange)}
.app-dot{position:absolute;width:22px;height:22px;border-radius:50%;background:var(--gold)}
.app-tabs{position:absolute;left:0;right:0;bottom:0;height:50px;background:rgba(0,0,0,.4);display:flex;justify-content:space-around;align-items:center}
.app-tabs span{width:18px;height:18px;border-radius:4px;border:2px solid #8d7e72}

/* ribbons */
.ribbon{position:absolute;height:68px;background:var(--ink);color:var(--orange);font-family:"Oswald",sans-serif;font-size:44px;line-height:68px;padding:0 30px;letter-spacing:1px}
.ribbon.tail-left::before{content:"";position:absolute;top:14px;left:-30px;width:0;height:0;border-top:20px solid transparent;border-bottom:20px solid transparent;border-right:30px solid var(--ink)}
.ribbon.both::before,.ribbon.both::after{content:"";position:absolute;top:14px;width:0;height:0;border-top:20px solid transparent;border-bottom:20px solid transparent}
.ribbon.both::before{left:-30px;border-right:30px solid var(--ink)}
.ribbon.both::after{right:-30px;border-left:30px solid var(--ink)}

.copy{position:absolute;font-size:15px;line-height:24px;color:var(--text)}
.copy p+p{margin-top:20px}
.copy b{color:#333}
.hl{color:var(--orange-dark);font-weight:700}
.divider{position:absolute;left:0;width:1200px;height:2px;background:var(--line)}

.achieve-item{position:absolute;display:flex;gap:22px;align-items:flex-start;width:330px;font-size:14px;line-height:22px}
.achieve-icon{flex:none;width:60px;height:60px}

/* coming soon */
.coming{position:absolute;left:0;top:3200px;width:1200px;height:1080px;background:var(--beige)}
.stores{position:absolute;left:436px;top:760px;display:flex;gap:56px}
.stores span{display:block;width:72px;height:80px;border-radius:12px}
.stores .s1{background:linear-gradient(135deg,#35b4d9,#7bc142 45%,#f5c21b 75%,#e8423a)}
.stores .s2{background:linear-gradient(180deg,#c9c9c9,#8a8a8a)}
.stores .s3{background:linear-gradient(180deg,#2aa1e6,#1478c4)}
.beta-box{position:absolute;left:332px;top:872px;width:536px;height:130px;background:var(--orange);border-radius:6px}
.beta-box h4{color:#fff;font-size:20px;font-weight:400;text-align:center;margin-top:20px}
.beta-box .signup{left:48px;top:64px;width:440px}

/* footer */
.footer{position:absolute;left:0;top:4280px;width:1200px;height:364px;background:linear-gradient(180deg,#2c2623,#1d1916);color:#fff}
.up{position:absolute;left:578px;top:24px;width:44px;height:44px}
.footer h5{position:absolute;left:0;width:1200px;top:90px;font-size:20px;font-weight:600;text-align:center}
.social{position:absolute;left:540px;top:138px;display:flex;gap:12px}
.social span{width:40px;height:40px;border:2px solid #fff;border-radius:50%}
.footer .legal,.footer .links{position:absolute;left:0;width:1200px;font-size:14px;color:#d9d2cc;text-align:center}
.footer .legal{top:236px}
.footer .links{top:280px}
</style>
</head>
<body>

<header class="hero">
  <div class="hero-photo" role="img" aria-label="Photo of a hand holding a smartphone"></div>
  <div class="hero-phone" aria-hidden="true"><div class="screen"><div class="app-avatar" style="top:40px"></div><div class="app-track" style="top:140px"><i style="width:55%"></i></div><div class="app-track" style="top:170px"><i style="width:35%"></i></div></div></div>
  <div class="brand"><span class="brand-dot"></span>Lumvra</div>
  <div class="contact-tab">Contact Us</div>
  <h1 class="hero-title">Lumvra is a Revolutionary &amp; Free Social Platform for Collaborative Addictions Quitting.</h1>
  <div class="subscribe-row">
    <svg width="56" height="48" viewBox="0 0 56 48" aria-hidden="true"><rect x="2" y="8" width="44" height="30" fill="none" stroke="#fff" stroke-width="3"/><path d="M2 8 L24 26 L46 8" fill="none" stroke="#fff" stroke-width="3"/><circle cx="44" cy="36" r="10" fill="#fff"/><path d="M39 36l4 4 6-7" fill="none" stroke="#2c2623" stroke-width="3"/></svg>
    <span>Subscribe below for the beta release and updates</span>
  </div>
  <div class="signup"><span class="field">Enter your e-mail address</span><span class="btn">Get the ticket!</span></div>
  <div class="devices" aria-hidden="true">
    <svg width="26" height="46" viewBox="0 0 26 46"><rect x="2" y="2" width="22" height="42" rx="3" fill="none" stroke="#bbb" stroke-width="3"/></svg>
    <svg width="40" height="52" viewBox="0 0 40 52"><rect x="2" y="2" width="36" height="48" rx="3" fill="none" stroke="#bbb" stroke-width="3"/></svg>
    <svg width="64" height="56" viewBox="0 0 64 56"><rect x="2" y="2" width="60" height="40" fill="#fff"/><rect x="26" y="42" width="12" height="8" fill="#fff"/><rect x="18" y="50" width="28" height="4" fill="#fff"/></svg>
  </div>
  <div class="pointer"></div>
</header>

<section class="features">
  <div class="feature" style="left:90px">
    <div class="feature-badge"><div class="disk">
      <svg width="96" height="96" viewBox="0 0 96 96" role="img" aria-label="Life ring icon"><circle cx="48" cy="48" r="36" fill="none" stroke="#e8412c" stroke-width="22"/><g stroke="#fff" stroke-width="22" fill="none" stroke-dasharray="18 38.5" transform="rotate(-54 48 48)"><circle cx="48" cy="48" r="36"/></g><circle cx="48" cy="48" r="25" fill="none" stroke="#b8321f" stroke-width="2"/><circle cx="48" cy="48" r="47" fill="none" stroke="#b8321f" stroke-width="2"/></svg>
    </div></div>
    <h3>Never be Alone</h3><p>Forget what you know - Lumvra makes it fun to quit.</p>
  </div>
  <div class="feature" style="left:450px">
    <div class="feature-badge"><div class="disk">
      <svg width="96" height="96" viewBox="0 0 96 96" role="img" aria-label="Star icon"><path d="M48 6l12.5 27 29.5 3.2-22 20 6.2 29L48 70.4 21.8 85.2 28 56.2 6 36.2l29.5-3.2z" fill="#f6b21b"/><path d="M48 6l12.5 27 29.5 3.2-22 20L48 48z" fill="#fbd162"/></svg>
    </div></div>
    <h3>Network Power</h3><p>Forget what you know - Lumvra makes it fun to quit.</p>
  </div>
  <div class="feature" style="left:810px">
    <div class="feature-badge"><div class="disk"><div class="art" role="img" aria-label="Illustration of a feathered chief headdress"></div></div></div>
    <h3>Stay Motivated</h3><p>Forget what you know - Lumvra makes it fun to quit.</p>
  </div>
</section>

<section style="position:absolute;left:0;top:1200px;width:1200px;height:640px">
  <div class="phone" style="left:160px;top:60px;width:260px;height:540px"><div class="screen glow-orange" role="img" aria-label="Illustration of a smiling clown mascot"></div></div>
  <div class="ribbon tail-left" style="left:552px;top:176px">FUN</div>
  <div class="copy" style="left:522px;top:288px;width:640px">
    <p>Forget what you know - <b>Lumvra makes it fun to quit.</b> The battle between your good and bad demons comes to life in our <span class="hl">gamified approach</span> for managing your campaigns.</p>
    <p>Lumvra gives you the opportunity to take an <b>active role</b> in helping your network to <b>smash</b> your common addictions as a team that's right, we converted the cessation process into a social game.</p>
  </div>
</section>
<div class="divider" style="top:1840px"></div>

<section style="position:absolute;left:0;top:1860px;width:1200px;height:640px">
  <div class="phone" style="left:792px;top:60px;width:256px;height:540px"><div class="screen glow-gold" role="img" aria-label="Illustration of a glowing light bulb"></div></div>
  <div class="ribbon tail-left" style="left:414px;top:220px">INSPIRE</div>
  <div class="copy" style="left:72px;top:332px;width:600px">
    <p>One of the most important factors for successful quitting is the ability to <b>stay inspired</b> during the process.</p>
    <p>That's why we designed Lumvra as a platform where you can inspire and be inspired by a supportive network of awesome Lumvra ninjas!</p>
  </div>
</section>
<div class="divider" style="top:2500px"></div>

<section style="position:absolute;left:0;top:2520px;width:1200px;height:680px;overflow:hidden">
  <div class="ribbon both" style="left:500px;top:96px">ACHIEVE</div>
  <div class="copy" style="left:300px;top:192px;width:600px;text-align:center">
    <p>Lumvra is built as a <b>pyramid of relationships</b> that makes use of the <b>Social Cognitive Theory</b>, to provide a powerful network of positive reinforcement.</p>
    <p>The bigger you make it the stronger you get.</p>
  </div>
  <div class="phone" style="left:472px;top:340px;width:256px;height:440px"><div class="screen glow-trophy" style="bottom:0" role="img" aria-label="Illustration of a gold trophy with laurels"></div></div>
  <div class="achieve-item" style="left:88px;top:420px"><svg class="achieve-icon" viewBox="0 0 64 64" aria-hidden="true"><path d="M14 8h36v14a18 18 0 0 1-36 0z" fill="var(--trophy)"/><path d="M14 12H6v6a10 10 0 0 0 10 10M50 12h8v6a10 10 0 0 1-10 10" fill="none" stroke="var(--trophy)" stroke-width="3"/><rect x="28" y="38" width="8" height="12" fill="var(--trophy)"/><rect x="18" y="50" width="28" height="8" fill="var(--trophy)"/></svg><span>Lumvra is built as a <b>pyramid of relationships</b> that makes use of the <b>Social Cognitive Theory.</b></span></div>
  <div class="achieve-item" style="left:88px;top:540px"><svg class="achieve-icon" viewBox="0 0 64 64" aria-hidden="true"><path d="M6 24h52l-6 30H12z" fill="var(--teal)"/><path d="M20 24l10-16M44 24L34 8" stroke="var(--teal)" stroke-width="4"/><path d="M22 32v16M32 32v16M42 32v16" stroke="#fff" stroke-width="3"/></svg><span>Lumvra is built as a <b>pyramid of relationships</b> that makes use of the <b>Social Cognitive Theory.</b></span></div>
  <div class="achieve-item" style="left:780px;top:420px"><svg class="achieve-icon" viewBox="0 0 64 64" aria-hidden="true"><path d="M14 8h36v14a18 18 0 0 1-36 0z" fill="var(--trophy)"/><path d="M14 12H6v6a10 10 0 0 0 10 10M50 12h8v6a10 10 0 0 1-10 10" fill="none" stroke="var(--trophy)" stroke-width="3"/><rect x="28" y="38" width="8" height="12" fill="var(--trophy)"/><rect x="18" y="50" width="28" height="8" fill="var(--trophy)"/></svg><span>Lumvra is built as a <b>pyramid of relationships</b> that makes use of the <b>Social Cognitive Theory.</b></span></div>
  <div class="achieve-item" style="left:780px;top:540px"><svg class="achieve-icon" viewBox="0 0 64 64" aria-hidden="true"><path d="M6 24h52l-6 30H12z" fill="var(--teal)"/><path d="M20 24l10-16M44 24L34 8" stroke="var(--teal)" stroke-width="4"/><path d="M22 32v16M32 32v16M42 32v16" stroke="#fff" stroke-width="3"/></svg><span>Lumvra is built as a <b>pyramid of relationships</b> that makes use of the <b>Social Cognitive Theory.</b></span></div>
</section>

<section class="coming">
  <div class="ribbon both" style="left:466px;top:100px">COMING SOON</div>
  <div class="phone" style="left:472px;top:184px;width:256px;height:540px">
    <div class="screen app" role="img" aria-label="Lumvra app home screen with profile and progress">
      <div class="app-bar"></div>
      <div class="app-avatar"></div>
      <div class="app-name">Welcome back</div>
      <div class="app-track" style="top:176px"><i style="width:62%"></i></div>
      <div class="app-dot" style="left:118px;top:168px"></div>
      <div class="app-track" style="top:214px"><i style="width:40%;background:var(--gold)"></i></div>
      <div class="app-track" style="top:252px"><i style="width:78%"></i></div>
      <div class="app-tabs"><span></span><span></span><span></span><span></span></div>
    </div>
  </div>
  <div class="stores" aria-hidden="true"><span class="s1"></span><span class="s2"></span><span class="s3"></span></div>
  <div class="beta-box">
    <h4>Subscribe below for the beta release and updates</h4>
    <div class="signup"><span class="field">Enter your e-mail address</span><span class="btn">Get the ticket!</span></div>
  </div>
</section>

<footer class="footer">
  <svg class="up" viewBox="0 0 44 44" aria-hidden="true"><circle cx="22" cy="22" r="20" fill="none" stroke="#fff" stroke-width="2"/><path d="M13 26l9-9 9 9" fill="none" stroke="#fff" stroke-width="2.5"/></svg>
  <h5>Join The Revolution</h5>
  <div class="social" aria-hidden="true"><span></span><span></span><span></span></div>
  <p class="legal">Copyright © 2015 Lumvra Ltd.</p>
  <p class="links">Contact Us / T&amp;C's / Privacy Policy</p>
</footer>

</body>
</html>
```